Stationery Design Project for Nimbora, Chicago

Nimbora, a street parking application which helps car drivers find a street parking spot by offering an ideal path along which to look for parking. This path is calculated by our algorithm based on data (e.g. historical data, baseball games schedule, etc.). Along this path the driver will find a spot and will also save 70% of the search time. Customer we target is reg. between 21 and 45 yo.

We envision something young, fresh, bright and original. Slightly abstract maybe. It should represent the idea and elements of finding street parking in the city, e.g. car(s), parking spot, people, city, etc. (just ideas!).

Logo is attached.

Requirement:
- Business Cards (2 Sided Full Color CMYK)
- Letterhead (1 Sided Full Color CMYK)
- Envelope (1 Sided Full Color CMYK)
- Sticker (1 Sided Full Color CMYK), round with a 2inch diameter.

Reason: We're starting to get more and more designs and need more time to look into all of them. Very exciting!! Thanks to everybody!

Hi all, we're in the process of selecting our favs. Though choices!!! Really good submissions. Will keep you posted and sorry for the delay.

Target Market(s)

Car drivers and owners between 21 and 45

Industry/Entity Type

Parking

Requirements
Must have
• Sticker should be round and include company URL nimbora.com and the new logo which we will attach soon.
Should not have
• Should not be too serious or boring.

```html
<!DOCTYPE html>
<html lang="en">
<head>
<meta charset="utf-8">
<title>Nimbora Business Card</title>
<link rel="stylesheet" href="https://fonts.googleapis.com/css2?family=Open+Sans:wght@400;600;700&display=swap">
<style>
  :root {
    --page-bg: #ecebe8;
    --card-white: #ffffff;
    --card-edge: #b9b9b9;
    --blue-light: #2aa3de;
    --blue-mid: #2277c6;
    --blue-deep: #2f3f98;
    --swoosh: #141414;
    --ink: #3a3a3a;
    --brand-ink: #333338;
    --divider: #c4c4c4;
    --lot-light: #8f959c;
    --lot-dark: #5d636b;
  }
  * { margin: 0; padding: 0; box-sizing: border-box; }
  html, body {
    width: 1200px;
    height: 1034px;
    overflow: hidden;
    background: var(--page-bg);
    font-family: "Open Sans", Arial, sans-serif;
  }
  .canvas { position: relative; width: 1200px; height: 1034px; }

  .card {
    position: absolute;
    width: 738px;
    height: 422px;
    border-radius: 22px;
    overflow: hidden;
  }

  /* Front side */
  .card--front {
    left: 74px;
    top: 59px;
    background: var(--card-white);
    border: 1.5px solid var(--card-edge);
  }
  .front-band { position: absolute; left: 0; top: 0; }
  .holder {
    position: absolute;
    right: 60px;
    top: 18px;
    text-align: right;
    color: #fff;
  }
  .holder__name { font-size: 27px; font-weight: 700; line-height: 1.2; }
  .holder__title { font-size: 20px; font-weight: 400; line-height: 1.2; }

  .brand {
    position: absolute;
    left: 56px;
    top: 124px;
    display: flex;
    align-items: center;
    gap: 22px;
  }
  .brand__dot {
    width: 124px;
    height: 124px;
    border-radius: 50%;
    background: var(--blue-mid);
  }
  .brand__name {
    font-size: 76px;
    font-weight: 600;
    color: var(--brand-ink);
    letter-spacing: 1px;
  }

  .contact {
    position: absolute;
    left: 46px;
    top: 296px;
    list-style: none;
    font-size: 18px;
    color: var(--ink);
    line-height: 26px;
  }
  .contact li { display: flex; align-items: center; gap: 10px; }
  .contact svg { width: 16px; height: 16px; flex: none; }
  .divider {
    position: absolute;
    left: 262px;
    top: 350px;
    width: 2px;
    height: 52px;
    background: var(--divider);
  }
  .address {
    position: absolute;
    left: 291px;
    top: 350px;
    font-size: 18px;
    line-height: 26px;
    color: var(--ink);
    font-style: normal;
  }

  /* Back side */
  .card--back {
    left: 367px;
    top: 528px;
    background: linear-gradient(90deg, var(--blue-light) 0%, var(--blue-mid) 60%, var(--blue-deep) 100%);
  }
  .back-mark {
    position: absolute;
    left: 47px;
    top: 102px;
    width: 212px;
    height: 212px;
    border-radius: 50%;
    background: var(--blue-deep);
    display: flex;
    align-items: center;
    justify-content: center;
  }
  .back-mark__name {
    font-size: 38px;
    font-weight: 600;
    color: #fff;
  }
  .lot-photo {
    position: absolute;
    left: 323px;
    top: 63px;
    width: 415px;
    height: 296px;
    background:
      linear-gradient(90deg, var(--blue-light) 0%, rgba(42,163,222,0) 14%),
      linear-gradient(180deg, var(--lot-light), var(--lot-dark) 50%, var(--lot-light));
  }
</style>
</head>
<body>
<main class="canvas">

  <section class="card card--front" aria-label="Business card front">
    <svg class="front-band" width="738" height="422" viewBox="0 0 738 422" aria-hidden="true">
      <defs>
        <linearGradient id="bandBlue" x1="0" y1="0" x2="1" y2="0">
          <stop offset="0" stop-color="#2aa3de"/>
          <stop offset="0.55" stop-color="#2277c6"/>
          <stop offset="1" stop-color="#2f3f98"/>
        </linearGradient>
      </defs>
      <path d="M0 0 H738 V222 C560 40 250 20 0 92 Z" fill="url(#bandBlue)"/>
      <path d="M0 92 C250 20 560 40 738 222 V238 C560 62 250 40 0 104 Z" fill="#141414"/>
      <path d="M0 104 C250 40 560 62 738 238 V244 C560 72 250 52 0 110 Z" fill="#ffffff"/>
    </svg>

    <div class="holder">
      <p class="holder__name">Your Name</p>
      <p class="holder__title">Title</p>
    </div>

    <div class="brand">
      <span class="brand__dot" aria-hidden="true"></span>
      <span class="brand__name">Nimbora</span>
    </div>

    <ul class="contact">
      <li>
        <svg viewBox="0 0 16 16" aria-hidden="true"><path d="M4 2 L6.5 5 L5 6.8 C6 8.8 7.2 10 9.2 11 L11 9.5 L14 12 L12.5 14 C7 13.5 2.5 9 2 3.5 Z" fill="#333"/></svg>
        +1 312 555 0148
      </li>
      <li>
        <svg viewBox="0 0 16 16" aria-hidden="true"><rect x="4.5" y="1" width="7" height="14" rx="1.5" fill="#333"/><rect x="6" y="3" width="4" height="7" fill="#fff"/></svg>
        +1 312 555 0192
      </li>
      <li>
        <svg viewBox="0 0 16 16" aria-hidden="true"><rect x="1.5" y="3.5" width="13" height="9" rx="1" fill="#333"/><path d="M2 4 L8 9 L14 4" stroke="#fff" stroke-width="1.4" fill="none"/></svg>
        info@nimbora.com
      </li>
      <li>
        <svg viewBox="0 0 16 16" aria-hidden="true"><circle cx="8" cy="8" r="6.5" fill="#333"/><path d="M1.5 8 H14.5" stroke="#fff" stroke-width="1"/></svg>
        www.nimbora.com
      </li>
    </ul>

    <span class="divider" aria-hidden="true"></span>
    <address class="address">
      Complex Name, Street Name<br>
      Area, City Name,000 000
    </address>
  </section>

  <section class="card card--back" aria-label="Business card back">
    <div class="back-mark">
      <span class="back-mark__name">Nimbora</span>
    </div>
    <div class="lot-photo" role="img" aria-label="Aerial photo of a parking lot with rows of parked cars"></div>
  </section>

</main>
</body>
</html>
```